Business Card for Industrial Distributor

We need a business card design for an industrial distributor. We sell machine parts for the manufacturing and oil industry. We would like the cards to look clean and modern but with a touch of industry.

Our colors are blue/white.

Please feel free to visit our website www.korvelpartsco.com

Target Market(s)

mexican manufacturers in the automobile/aerospace industry

Industry/Entity Type

Industrial

Colors
ffffff
0555a3

```html
<!DOCTYPE html>
<html lang="en">
<head>
<meta charset="utf-8">
<title>Korvel Business Card</title>
<link href="https://fonts.googleapis.com/css2?family=Lato:wght@400;700;900&display=swap" rel="stylesheet">
<style>
  :root {
    --stage: #3d3d3d;
    --brand-blue: #0555a3;
    --deep-blue: #1f3a93;
    --light-blue: #2a72b8;
    --grey-band: #8e8f92;
    --text-grey: #8a8a8a;
    --white: #ffffff;
  }
  * { margin: 0; padding: 0; box-sizing: border-box; }
  html, body { width: 1200px; height: 810px; overflow: hidden; background: var(--stage); }
  body { position: relative; font-family: "Lato", sans-serif; }

  .card {
    position: absolute;
    width: 540px;
    height: 310px;
    overflow: hidden;
    box-shadow: 0 8px 24px rgba(0,0,0,0.35);
  }

  /* Back side */
  .card-back {
    left: 90px; top: 70px;
    background: radial-gradient(ellipse at 45% 35%, var(--light-blue) 0%, var(--brand-blue) 45%, #2b56a0 100%);
    color: var(--white);
  }
  .back-mark {
    position: absolute;
    left: 0; right: 0; top: 100px;
    display: flex; justify-content: center; align-items: center; gap: 14px;
  }
  .mark-dot {
    width: 40px; height: 40px; border-radius: 50%;
    background: var(--white);
  }
  .back-mark .brand-name {
    font-size: 52px; font-weight: 900; color: var(--white); letter-spacing: 0.5px;
  }
  .back-web {
    position: absolute; left: 0; right: 0; bottom: 36px;
    text-align: center; font-size: 13px; letter-spacing: 0.3px;
  }

  /* Front side */
  .card-front { left: 570px; top: 430px; background: var(--white); }
  .front-wave { position: absolute; inset: 0; }
  .front-logo {
    position: absolute; left: 34px; top: 36px;
    display: flex; align-items: center; gap: 12px;
  }
  .front-logo .mark-dot { background: var(--brand-blue); width: 44px; height: 44px; }
  .front-logo .brand-name {
    font-size: 50px; font-weight: 900; color: var(--deep-blue); letter-spacing: 0.5px;
  }
  .holder {
    position: absolute; right: 118px; top: 36px; text-align: right;
  }
  .holder-name { font-size: 22px; font-weight: 700; color: var(--deep-blue); }
  .holder-title { font-size: 13px; color: var(--text-grey); margin-top: 2px; }

  .company {
    position: absolute; left: 34px; top: 122px;
    font-size: 12.5px; line-height: 1.35; color: var(--text-grey);
  }
  .company-name { color: var(--deep-blue); font-weight: 700; font-size: 13.5px; }
  .contact-list { list-style: none; margin-top: 8px; }
  .contact-list li { display: flex; align-items: center; gap: 8px; }
  .contact-list svg { width: 13px; height: 13px; fill: var(--deep-blue); flex: none; }

  .front-web {
    position: absolute; right: 30px; bottom: 30px;
    color: var(--white); font-size: 13px; letter-spacing: 0.3px;
  }
</style>
</head>
<body>

  <section class="card card-back" aria-label="Card back">
    <div class="back-mark">
      <span class="mark-dot"></span>
      <span class="brand-name">Korvel</span>
    </div>
    <p class="back-web">www.korvelpartsco.com</p>
  </section>

  <section class="card card-front" aria-label="Card front">
    <svg class="front-wave" viewBox="0 0 540 310" preserveAspectRatio="none" aria-hidden="true">
      <defs>
        <linearGradient id="waveBlue" x1="1" y1="0" x2="0" y2="1">
          <stop offset="0" stop-color="#2a72b8"/>
          <stop offset="1" stop-color="#0555a3"/>
        </linearGradient>
      </defs>
      <path d="M0,274 Q430,258 478,0 L540,0 V310 H0 Z" fill="var(--grey-band)"/>
      <path d="M0,283 Q436,265 485,0 L540,0 V310 H0 Z" fill="var(--white)"/>
      <path d="M0,289 Q442,271 491,0 L540,0 V310 H0 Z" fill="url(#waveBlue)"/>
    </svg>

    <div class="front-logo">
      <span class="mark-dot"></span>
      <span class="brand-name">Korvel</span>
    </div>

    <div class="holder">
      <p class="holder-name">Daniel Reyes</p>
      <p class="holder-title">President &amp; CEO</p>
    </div>

    <div class="company">
      <p class="company-name">korvel international Corp.</p>
      <p>2840 Harbor Mill Rd,</p>
      <p>Laredo, TX 78041</p>
      <ul class="contact-list">
        <li>
          <svg viewBox="0 0 16 16"><path d="M3 2c1-1 2 0 3 1.5S6 6 5.5 6.5c1 2 2 3 4 4 .5-.5 1.5-1.5 3-.5s2.5 2 1.5 3S11 15 7 11 2 3 3 2z"/></svg>
          (555) 214 - 3080
        </li>
        <li>
          <svg viewBox="0 0 16 16"><path d="M4 1h8v4H4zM1 6h14v6h-3v3H4v-3H1zM5 10v4h6v-4z"/></svg>
          (555) 214 - 3084
        </li>
        <li>
          <svg viewBox="0 0 16 16"><path d="M1 3h14v10H1zM2 4l6 5 6-5v-.5H2z" fill-rule="evenodd"/></svg>
          sales@korvelpartsco.com
        </li>
      </ul>
    </div>

    <p class="front-web">www.korvelpartsco.com</p>
  </section>

</body>
</html>
```